Business Card Design

We are looking for a business card designed for our landscaping company. We do landscaping installation & Maintenance Services. We would like to see designs that have basic landscaping in background. We also think it is important to have both of our names and phone numbers on the card. We need something that stands out a little whether it is shape of the card or thickness or design.

Business

Bramblewood Yardworks, bramblewoodyard@mailvista.net, Owen Platt 555-273-9104, Daniel Korbin 555-618-3927

```html
<!DOCTYPE html>
<html lang="en">
<head>
<meta charset="utf-8">
<title>Bramblewood Yardworks — Business Card</title>
<link rel="stylesheet" href="https://fonts.googleapis.com/css2?family=Tinos&display=swap">
<style>
  :root {
    --page-bg: #d9d6d0;
    --card-bg: #050505;
    --ink: #eeeeee;
    --ink-soft: #d6d6d6;
    --rule: #e8e8e8;
    --glow: rgba(255, 255, 255, 0.35);
  }
  * { margin: 0; padding: 0; box-sizing: border-box; }
  html, body {
    width: 1200px;
    height: 902px;
    overflow: hidden;
    background: var(--page-bg);
  }
  .business-card {
    position: absolute;
    left: 100px;
    top: 165px;
    width: 1000px;
    height: 571px;
    background: var(--card-bg);
    font-family: "Tinos", "Times New Roman", serif;
    color: var(--ink);
    overflow: hidden;
    box-shadow: 0 6px 18px rgba(0, 0, 0, 0.25);
  }
  .company-name {
    position: absolute;
    left: 110px;
    top: 78px;
    font-size: 72px;
    font-weight: 400;
    letter-spacing: 0.5px;
    white-space: nowrap;
    text-shadow: 0 0 6px var(--glow);
  }
  .rule {
    position: absolute;
    height: 6px;
    background: var(--rule);
  }
  .rule--top-right { right: 0; top: 168px; width: 205px; }
  .rule--left { left: 0; top: 300px; width: 250px; }
  .divider {
    position: absolute;
    left: 560px;
    top: 205px;
    width: 3px;
    height: 235px;
    background: var(--rule);
    transform: rotate(-6deg);
    transform-origin: top center;
  }
  .contact {
    position: absolute;
    white-space: nowrap;
  }
  .contact__name {
    font-size: 48px;
    line-height: 1;
    text-shadow: 0 0 5px var(--glow);
  }
  .contact__phone {
    display: flex;
    align-items: center;
    gap: 12px;
    font-size: 32px;
    color: var(--ink-soft);
    margin-top: 8px;
  }
  .contact--left { right: 470px; top: 250px; text-align: right; }
  .contact--left .contact__phone { justify-content: flex-end; }
  .contact--right { left: 600px; top: 225px; }
  .phone-icon { width: 24px; height: 24px; flex: none; }
  .email {
    position: absolute;
    left: 535px;
    top: 480px;
    font-size: 30px;
    color: var(--ink-soft);
    white-space: nowrap;
  }
</style>
</head>
<body>
  <main class="business-card">
    <h1 class="company-name">Bramblewood Yardworks</h1>
    <div class="rule rule--top-right"></div>
    <div class="rule rule--left"></div>
    <div class="divider"></div>

    <section class="contact contact--left">
      <p class="contact__name">Owen Platt</p>
      <p class="contact__phone">
        <span>555-273-9104</span>
        <svg class="phone-icon" viewBox="0 0 24 24" aria-hidden="true">
          <rect width="24" height="24" rx="2" fill="#eeeeee"/>
          <path d="M8 5c-1.5 1-2 2.5-1.2 5 1 3 3.5 6 6.5 7.5 1.8.8 3.2.4 4.2-.8l-2.6-2.4-1.8 1c-1.6-.8-3.2-2.6-3.8-4.2l1.3-1.5z" fill="#050505"/>
        </svg>
      </p>
    </section>

    <section class="contact contact--right">
      <p class="contact__name">Daniel Korbin</p>
      <p class="contact__phone">
        <svg class="phone-icon" viewBox="0 0 24 24" aria-hidden="true">
          <rect width="24" height="24" rx="2" fill="#eeeeee"/>
          <path d="M8 5c-1.5 1-2 2.5-1.2 5 1 3 3.5 6 6.5 7.5 1.8.8 3.2.4 4.2-.8l-2.6-2.4-1.8 1c-1.6-.8-3.2-2.6-3.8-4.2l1.3-1.5z" fill="#050505"/>
        </svg>
        <span>555-618-3927</span>
      </p>
    </section>

    <p class="email">bramblewoodyard@mailvista.net</p>
  </main>
</body>
</html>
```